Dalvick's Business Card

I need some designs for a new business card including the new logo attached. An old example of our business card is also attached to show all the data that should be included on the new design.
**I added some more examples someone had mocked up**

Contact Information for Business Card

Should include all info on other examples uploaded.

```html
<!DOCTYPE html>
<html lang="en">
<head>
<meta charset="utf-8">
<title>Dalvick's Business Card</title>
<link href="https://fonts.googleapis.com/css2?family=Poppins:wght@400;500;600;700&family=Oswald:wght@600&display=swap" rel="stylesheet">
<style>
  :root {
    --bg: #e4e4e4;
    --paper: #f6f6f6;
    --brand-blue: #0a73c0;
    --accent-red: #e52330;
    --ink: #2a2a2a;
    --white: #ffffff;
  }
  * { box-sizing: border-box; margin: 0; padding: 0; }
  html, body { width: 1200px; height: 930px; overflow: hidden; }
  body {
    background: var(--bg);
    font-family: "Poppins", sans-serif;
    position: relative;
  }
  .card {
    position: absolute;
    top: 310px;
    width: 540px;
    height: 309px;
    box-shadow: 0 10px 24px rgba(0,0,0,0.12);
  }
  .card--front { left: 40px; background: var(--paper); }
  .card--back { left: 620px; background: var(--brand-blue); color: var(--white); }

  .brand {
    position: absolute;
    display: flex;
    align-items: center;
    gap: 12px;
  }
  .brand__dot {
    width: 40px; height: 40px; border-radius: 50%;
  }
  .brand__name {
    font-weight: 700;
    font-size: 44px;
    letter-spacing: 1px;
    line-height: 1;
  }
  .card--front .brand { top: 42px; left: 150px; }
  .card--front .brand__dot { background: var(--accent-red); }
  .card--front .brand__name { color: var(--brand-blue); }

  .owner {
    position: absolute;
    left: 40px; top: 132px;
    font-family: "Oswald", sans-serif;
    font-weight: 600;
    font-size: 34px;
    color: var(--brand-blue);
    letter-spacing: 0.5px;
  }
  .divider-v {
    position: absolute;
    left: 262px; top: 136px;
    width: 1px; height: 48px;
    background: #cfcfcf;
  }
  .contact {
    position: absolute;
    left: 282px; top: 134px;
    list-style: none;
    font-size: 16px;
    color: var(--ink);
  }
  .contact li { display: flex; align-items: center; gap: 10px; height: 26px; }
  .contact svg { width: 16px; height: 16px; fill: var(--accent-red); }
  .rule {
    position: absolute;
    left: 40px; right: 40px; top: 214px;
    height: 2px; background: var(--brand-blue);
  }
  .credentials {
    position: absolute;
    left: 40px; top: 230px;
    font-size: 15px; font-weight: 600;
    letter-spacing: 0.5px;
  }
  .credentials__blue { color: var(--brand-blue); }
  .credentials__sep { color: var(--ink); margin: 0 8px; }
  .credentials__red { color: var(--accent-red); }

  .card--back .brand { top: 60px; left: 150px; }
  .card--back .brand__dot { background: var(--white); }
  .card--back .brand__name { color: var(--white); }
  .back__rule {
    position: absolute;
    left: 40px; right: 40px; top: 172px;
    height: 1px; background: var(--white);
  }
  .service-area {
    position: absolute;
    left: 0; right: 0; top: 138px;
    text-align: center;
    font-weight: 600; font-size: 17px;
  }
  .cta {
    position: absolute;
    left: 0; right: 0; top: 186px;
    text-align: center;
    font-weight: 500; font-size: 12.5px;
    letter-spacing: 0.6px;
  }
</style>
</head>
<body>
  <section class="card card--front">
    <div class="brand">
      <span class="brand__dot"></span>
      <span class="brand__name">DALVICK'S</span>
    </div>
    <div class="owner">MARK DALVICK</div>
    <div class="divider-v"></div>
    <ul class="contact">
      <li>
        <svg viewBox="0 0 24 24" aria-hidden="true"><path d="M6.6 10.8a15.1 15.1 0 0 0 6.6 6.6l2.2-2.2a1 1 0 0 1 1-.25 11.4 11.4 0 0 0 3.6.57 1 1 0 0 1 1 1V20a1 1 0 0 1-1 1A17 17 0 0 1 3 4a1 1 0 0 1 1-1h3.5a1 1 0 0 1 1 1c0 1.25.2 2.45.57 3.57a1 1 0 0 1-.25 1z"/></svg>
        555.014.2290
      </li>
      <li>
        <svg viewBox="0 0 24 24" aria-hidden="true"><path d="M2 5h20v14H2z M2 5l10 8 10-8" fill="none" stroke="#e52330" stroke-width="2"/></svg>
        hvacdalvick@mailbox.com
      </li>
    </ul>
    <div class="rule"></div>
    <p class="credentials">
      <span class="credentials__blue">LICENSED &amp; INSURED</span><span class="credentials__sep">|</span><span class="credentials__red">FAMILY OWNED &amp; OPERATED</span>
    </p>
  </section>

  <section class="card card--back">
    <div class="brand">
      <span class="brand__dot"></span>
      <span class="brand__name">DALVICK'S</span>
    </div>
    <p class="service-area">Serves Brookfield, IA &amp; Surrounding Areas</p>
    <div class="back__rule"></div>
    <p class="cta">CALL TODAY FOR ALL YOUR HVAC, REFRIGERATION &amp; PLUMBING NEEDS</p>
  </section>
</body>
</html>
```